Brindle Children's Center - Child Care brochure

I just bought a new child care and completely renovated the space. We are also designing a new website, so I need the brochure to match that with updated info. www.brindlechildrenscenter.com - Information on there is current. We expect to have the new one up and running in the next few days. We have new photo's that I'd like to be added to the flyer too. ps. the boys in the pictures are mine, so i would appreciate one of them being added :). support@netcrafterhub.com has details on the website (dev.brindlechildrenscenter.com). The child care program is only open during the ski season - i.e. a resort facility catering to high end clients.
I'm attaching the the website information, the flyer I created, logo files and pictures.

Target Market(s)

Parents of young children

Font styles to use
Other font styles liked:
• "Things we said" & "Calibri Light"

Colors
cfeae6
fef1ee

Requirements
Must have
• Pictures of children. sleek design - winter, mountain theme. Check with website designer on new website.
Nice to have
• prices included
Should not have
• Kid like artwork

```html
<!DOCTYPE html>
<html lang="en">
<head>
<meta charset="utf-8">
<title>Brindle Children's Center – Brochure</title>
<link rel="stylesheet" href="https://fonts.googleapis.com/css2?family=Carlito:wght@400;700&family=Mountains+of+Christmas:wght@700&display=swap">
<style>
  :root {
    --page-bg: #e4e6e8;
    --sheet: #f7f5f6;
    --sheet-shade: #eeecee;
    --side-panel: #d3d2d6;
    --ink: #4a4a4d;
    --ink-soft: #5d5d62;
    --blush: #fef1ee;
    --blush-frame: #f1d6cc;
    --mint: #cfeae6;
    --snow: #eef3f8;
    --sky: #9db6cf;
    --pine: #5a6e6a;
    --room: #d9d2c9;
  }
  * { box-sizing: border-box; margin: 0; padding: 0; }
  html, body { width: 1200px; height: 900px; overflow: hidden; }
  body {
    background: var(--page-bg);
    font-family: "Carlito", "Calibri", sans-serif;
    color: var(--ink);
    position: relative;
  }
  .brochure {
    position: absolute;
    left: 75px; top: 50px;
    width: 1050px; height: 800px;
    display: grid;
    grid-template-columns: repeat(3, 1fr);
    box-shadow: 0 6px 24px rgba(0,0,0,.12);
  }
  .panel { position: relative; padding: 30px 32px; }
  .panel--welcome, .panel--services {
    background: linear-gradient(180deg, var(--sheet) 0%, var(--sheet-shade) 100%);
  }
  .panel--services { border-left: 1px solid #e2dfe1; }
  .panel--details { background: var(--side-panel); padding: 34px 30px; }

  .photo { display: block; }
  .photo--playroom {
    height: 300px; border-radius: 26px;
    background: linear-gradient(160deg, var(--mint) 0%, var(--blush) 45%, var(--room) 100%);
    display: flex; align-items: flex-start; justify-content: center;
    padding-top: 60px;
  }
  .center-name {
    font-family: "Carlito", sans-serif; font-weight: 700;
    font-size: 20px; color: var(--ink);
  }
  .headline {
    font-family: "Mountains of Christmas", cursive;
    font-weight: 700; color: var(--ink);
    text-align: center; line-height: 1.05;
  }
  .panel--welcome .headline { font-size: 34px; margin: 34px 0 24px; }
  .body-copy { font-size: 15px; line-height: 1.5; text-align: center; color: var(--ink-soft); }
  .body-copy + .body-copy { margin-top: 18px; }

  .portraits { display: flex; justify-content: space-between; align-items: flex-start; padding: 0 12px; }
  .portrait {
    width: 120px; height: 120px; border-radius: 50%;
    border: 6px solid var(--blush-frame);
  }
  .portrait--boy { margin-top: 26px; background: radial-gradient(circle at 50% 40%, #e8cbb8 0%, #6d7da0 70%); }
  .portrait--girl { background: radial-gradient(circle at 50% 40%, #ecd4c4 0%, #a7a3a8 70%); }
  .panel--services .headline { font-size: 32px; margin: 14px 0 16px; text-align: right; padding-right: 10px; }
  .panel--services .body-copy { font-size: 14px; line-height: 1.45; text-align: left; }
  .photo--resort {
    position: absolute; left: 32px; right: 32px; bottom: 34px;
    height: 170px; border-radius: 18px;
    background: linear-gradient(180deg, var(--sky) 0%, var(--snow) 45%, #c9d3da 70%, var(--pine) 100%);
  }

  .service + .service { margin-top: 22px; }
  .service__title { font-size: 15px; font-weight: 700; text-align: center; margin-bottom: 5px; color: var(--ink); }
  .service__text { font-size: 13.5px; line-height: 1.42; color: var(--ink-soft); }
</style>
</head>
<body>
  <main class="brochure">
    <section class="panel panel--welcome">
      <div class="photo photo--playroom" role="img" aria-label="Photo of two girls playing in the bright playroom beneath the center's sign">
        <span class="center-name">Brindle Children's Center</span>
      </div>
      <h1 class="headline">Welcome to<br>Brindle Children's Center</h1>
      <p class="body-copy">When you hit the slopes, you want to make sure your child has an enjoyable day too. At the Brindle Children's Center, you can be sure that your child receives the best care possible – and has a great time to boot!</p>
      <p class="body-copy">Located on-site at the world-famous Brindle Ski Resort, you can drop off your child at a safe and fun care center and literally step out the door and hit the slopes.</p>
    </section>

    <section class="panel panel--services">
      <div class="portraits">
        <div class="portrait portrait--boy" role="img" aria-label="Portrait photo of a smiling young boy"></div>
        <div class="portrait portrait--girl" role="img" aria-label="Portrait photo of a toddler reading a book"></div>
      </div>
      <h2 class="headline">Our Services</h2>
      <p class="body-copy">The Brindle Children's Center is a full service child care facility that caters to children from 2 months old to 10 years old. Infants and young children can play, create and learn in the center. Children ages 4 and up can join Brindle's legendary Ridgeline Ski School and spend the day learning from one of Brindle's friendly instructors. Our center is designed to stimulate curious young minds with areas set up for creative arts, social/emotional learning in the dramatic play area, blocks &amp; physical motor movement area, and a math and science discovery area. We provide 3 nutritious meals throughout the day.</p>
      <div class="photo photo--resort" role="img" aria-label="Photo of the snowy mountain resort and lodge in winter"></div>
    </section>

    <section class="panel panel--details">
      <article class="service">
        <h3 class="service__title">Infant care</h3>
        <p class="service__text">Our infant care area is open from ages 2 months to walking toddlers. The area is safely enclosed to cater to the specific needs of an infant, with dim lightening, developmentally appropriate equipment and materials. The staff to children's ratio is low to provide the best care.</p>
      </article>
      <article class="service">
        <h3 class="service__title">Young Children</h3>
        <p class="service__text">We know how to keep young minds busy. Your child will be giving opportunities to create art, play musical instruments, move, think and listen that challenges their imagination.</p>
      </article>
      <article class="service">
        <h3 class="service__title">Ski School</h3>
        <p class="service__text">The Brindle Children's Center works closely with the famous Ridgeline Ski School. If you wish to have your child participate in the group ski lesson (for ages 4 and up), the mini adventure package can be purchased at the ski school office and includes a half day at The Brindle Children's Center.</p>
      </article>
      <article class="service">
        <h3 class="service__title">Après-ski care</h3>
        <p class="service__text">After a fantastic day on the slopes, you can now enjoy social events or activities child free. We offer child care on Friday and Saturday evenings from 4:30 – 6:30PM. Don't forget to make reservations though at reservations@brindlechildrenscenter.com</p>
      </article>
      <article class="service">
        <h3 class="service__title">Need eveing care?</h3>
        <p class="service__text">Pick up a recommended babysitter list at the front desk. Professionals are at least 18 years old, CPR &amp; First Aid trained, background checked, and experience is listed on the sheet. Evening babysitters are not associated with the Brindle Children's Center after hours, and therefore need to be paid directly for services.</p>
      </article>
    </section>
  </main>
</body>
</html>
```